Business Card Design Project

We are a construction company in Orange County, CA. We need a two sided business card. We would like the back to be our logo with web URL. Front should included Name, title, address, phone, fax and email address.

our address is
627 West Dorrance Blvd, Suite 308
Anaheim, CA 92718

Our logo files are attached.

Construction

```html
<!DOCTYPE html>
<html lang="en">
<head>
<meta charset="utf-8">
<title>Alven Business Card</title>
<link href="https://fonts.googleapis.com/css2?family=Source+Sans+3:wght@400;600;700&display=swap" rel="stylesheet">
<style>
  :root {
    --brand-blue: #1e4b7d;
    --ink: #333333;
    --ink-soft: #555555;
    --card-bg: #ffffff;
    --card-edge: #6b5240;
    --page-bg: #ece7e1;
  }
  * { margin: 0; padding: 0; box-sizing: border-box; }
  html, body {
    width: 1200px; height: 429px; overflow: hidden;
    background: var(--page-bg);
    font-family: "Source Sans 3", "Myriad Pro", sans-serif;
  }
  .stage { position: relative; width: 1200px; height: 429px; }
  .card {
    position: absolute; top: 53px; width: 526px; height: 301px;
    background: var(--card-bg);
    border: 1px solid var(--card-edge);
    border-radius: 20px;
  }
  .card--front { left: 43px; }
  .card--back { left: 600px; }

  .edge-tab {
    position: absolute; top: 133px; width: 11px; height: 134px;
    background: var(--brand-blue);
  }
  .edge-tab--left { left: -1px; border-radius: 0 8px 8px 0; }
  .edge-tab--right { right: -1px; border-radius: 8px 0 0 8px; }

  .brand {
    position: absolute; left: 0; right: 0;
    display: flex; justify-content: center; align-items: center; gap: 14px;
    color: var(--brand-blue);
  }
  .card--front .brand { top: 42px; }
  .card--back .brand { top: 104px; }
  .brand__mark {
    width: 34px; height: 34px; background: var(--brand-blue);
  }
  .brand__name {
    font-weight: 700; font-size: 58px; line-height: 64px;
  }

  .contact { position: absolute; top: 150px; left: 0; right: 0; text-align: center; color: var(--ink); }
  .contact__name { font-size: 19px; color: var(--brand-blue); }
  .contact__name strong { font-weight: 700; }
  .contact__lines { margin-top: 12px; font-size: 14px; line-height: 18px; }
  .contact__item { display: inline-flex; align-items: center; gap: 4px; margin: 0 3px; }
  .contact__item svg { width: 10px; height: 10px; fill: var(--ink); }
  .contact__address { margin-top: 12px; font-size: 14.5px; }

  .back-url {
    position: absolute; top: 204px; left: 0; right: 0; text-align: center;
    font-size: 15px; letter-spacing: 3px; color: var(--ink-soft);
  }
</style>
</head>
<body>
<main class="stage">
  <section class="card card--front" aria-label="Card front">
    <div class="edge-tab edge-tab--left"></div>
    <div class="edge-tab edge-tab--right"></div>
    <div class="brand">
      <span class="brand__mark" aria-hidden="true"></span>
      <span class="brand__name">Alven</span>
    </div>
    <div class="contact">
      <div class="contact__name"><strong>Your Name,</strong> Title</div>
      <div class="contact__lines">
        <div>
          <span class="contact__item">
            <svg viewBox="0 0 10 10" aria-hidden="true"><path d="M2 0.5l2 2-1 1.3c.6 1.2 1.5 2.1 2.7 2.7L7 5.5l2 2L7.8 9.5C4 9 1 6 .5 2.2z"/></svg>
            01-234-5678
          </span>
          <span class="contact__item">
            <svg viewBox="0 0 10 10" aria-hidden="true"><path d="M2.5 0.5h4l1 2h-6zM0.5 3.5h9v4.5h-1.5v-1.5h-6v1.5h-1.5z"/></svg>
            01-234-5678
          </span>
        </div>
        <div>
          <span class="contact__item">
            <svg viewBox="0 0 10 10" aria-hidden="true"><path d="M0.5 2h9v6h-9zM1 2.5l4 3 4-3"/></svg>
            info@alvenbuild.com
          </span>
          <span class="contact__item">
            <svg viewBox="0 0 10 10" aria-hidden="true"><circle cx="5" cy="5" r="4.5"/></svg>
            www.alvenbuild.com
          </span>
        </div>
      </div>
      <div class="contact__address">627 West Dorrance Blvd, Suite 308, Anaheim, CA&nbsp; 92718</div>
    </div>
  </section>

  <section class="card card--back" aria-label="Card back">
    <div class="brand">
      <span class="brand__mark" aria-hidden="true"></span>
      <span class="brand__name">Alven</span>
    </div>
    <div class="back-url">www.alvenbuild.com</div>
  </section>
</main>
</body>
</html>
```